Covid 19 Exit Strategy one page brochure

I would like to design, and will need URGENT help, a brochure detailing a Covid 19 Exit Strategy plan. This brochure will need to be understood easily and the graphics inside should make it easy for people to understand without reading the entire text. This project is quite urgent and needs to be completed THIS WEEK - by Saturday may 16th at the latest. I am attaching two examples. I will provide the text.

```html
<!DOCTYPE html>
<html lang="en">
<head>
<meta charset="utf-8">
<title>Covid 19 – The Exit Strategy</title>
<link rel="stylesheet" href="https://fonts.googleapis.com/css2?family=Oswald:wght@500;600&family=Roboto+Condensed:wght@400&display=swap">
<style>
  :root {
    --page-bg: #3a3836;
    --navy: #1a3f8f;
    --navy-deep: #12307a;
    --royal: #2457b5;
    --sky: #5aa3dc;
    --ice-1: #ffffff;
    --ice-2: #eef5fb;
    --ice-3: #dcecf8;
    --icon-navy: #1d3f8c;
    --icon-light: #7db8ea;
    --red: #d9232a;
    --white: #ffffff;
    --text-dark: #4a5160;
  }
  * { box-sizing: border-box; margin: 0; padding: 0; }
  html, body { width: 1200px; height: 800px; overflow: hidden; }
  body { background: var(--page-bg); font-family: "Roboto Condensed", Arial, sans-serif; }

  .brochure {
    position: absolute; left: 329px; top: 20px;
    width: 541px; height: 760px; background: var(--white);
    overflow: hidden; box-shadow: 0 6px 18px rgba(0,0,0,.45);
  }

  /* Header */
  .hero { position: absolute; left: 0; top: 0; width: 541px; height: 240px;
    background: linear-gradient(180deg, var(--navy) 0%, var(--navy-deep) 100%); }
  .hero__band { position: absolute; inset: 0; }
  .hero__title { position: absolute; left: 30px; top: 30px; font-family: "Oswald", Impact, sans-serif;
    font-weight: 600; font-size: 40px; line-height: 46px; color: var(--white); letter-spacing: .3px; }
  .hero__title .accent { color: var(--red); }
  .hero__lead { position: absolute; left: 30px; top: 180px; width: 210px; color: var(--white);
    font-size: 10px; line-height: 13px; }
  .hero__map { position: absolute; left: 268px; top: 30px; width: 260px; height: 175px;
    border-radius: 40% 30% 35% 45%;
    background: radial-gradient(ellipse at 50% 50%, #c9d0da 0%, #aeb8c7 60%, rgba(36,87,181,0) 75%); }

  /* Measures grid */
  .measures { position: absolute; left: 0; top: 240px; width: 541px; height: 254px; }
  .measures__row { position: absolute; left: 0; width: 541px; height: 85px; }
  .measures__row--1 { top: 0; background: var(--ice-1); }
  .measures__row--2 { top: 85px; background: var(--ice-2); }
  .measures__row--3 { top: 170px; height: 84px; background: var(--ice-3); }
  .measures__panel { position: absolute; left: 0; top: 0; }
  .measure { position: absolute; display: flex; align-items: center; gap: 18px; font-size: 10px; line-height: 13px; }
  .measure--left { left: 36px; color: var(--white); }
  .measure--right { left: 313px; color: var(--text-dark); gap: 20px; }
  .measure--right .measure__text { width: 150px; }
  .measure--left .measure__text { width: 145px; }
  .measure svg { flex: none; }
  .divider { position: absolute; left: 32px; height: 1px; background: rgba(255,255,255,.45); }

  /* Highlights */
  .highlights { position: absolute; left: 0; top: 494px; width: 541px; height: 189px;
    background: radial-gradient(ellipse at 50% 40%, var(--royal) 0%, var(--navy) 55%, var(--navy-deep) 100%); }
  .highlight { position: absolute; top: 0; width: 163px; height: 189px; text-align: center; color: var(--white);
    font-size: 10px; line-height: 13px; }
  .highlight svg { position: absolute; left: 50%; top: 50px; transform: translateX(-50%); }
  .highlight__text { position: absolute; left: 10px; right: 10px; top: 110px; }
  .highlight--1 { left: 22px; } .highlight--2 { left: 185px; } .highlight--3 { left: 348px; }
  .highlights__rule { position: absolute; top: 24px; width: 1px; height: 145px; background: rgba(125,184,234,.45); }

  /* Footer */
  .closing { position: absolute; left: 0; top: 683px; width: 541px; height: 77px;
    display: flex; align-items: center; justify-content: center;
    font-family: "Oswald", Impact, sans-serif; font-weight: 500; font-size: 26px; color: var(--red); }
</style>
</head>
<body>
<main class="brochure">

  <header class="hero">
    <svg class="hero__band" width="541" height="240" viewBox="0 0 541 240">
      <polygon points="200,0 541,0 541,240 60,240" fill="#2a5fbf" opacity=".55"/>
    </svg>
    <h1 class="hero__title"><span class="accent">COVID 19</span><br>THE EXIT<br>STRATEGY</h1>
    <p class="hero__lead">To greadually phase out the restrictions imposed to curb the spread of coronavirus remaining cautious.</p>
    <div class="hero__map" role="img" aria-label="Map of the United States dotted with blue coronavirus particles"></div>
  </header>

  <section class="measures">
    <div class="measures__row measures__row--1"></div>
    <div class="measures__row measures__row--2"></div>
    <div class="measures__row measures__row--3"></div>
    <svg class="measures__panel" width="541" height="254" viewBox="0 0 541 254">
      <polygon points="0,0 310,0 220,254 0,254" fill="var(--sky)"/>
    </svg>
    <div class="divider" style="top:85px;width:230px"></div>
    <div class="divider" style="top:170px;width:200px"></div>

    <div class="measure measure--left" style="top:25px">
      <svg width="48" height="44" viewBox="0 0 48 44" fill="none" stroke="#fff" stroke-width="2.4">
        <path d="M4 4h40l3 11H1z"/><path d="M12 4l-2 11M20 4l-1 11M28 4l1 11M36 4l2 11"/>
        <rect x="5" y="15" width="38" height="27"/><rect x="11" y="21" width="26" height="15"/>
        <path d="M20 32l8-8M24 34l8-8"/>
      </svg>
      <p class="measure__text">Small business open with strict safety measures.</p>
    </div>
    <div class="measure measure--left" style="top:105px">
      <svg width="48" height="46" viewBox="0 0 48 46" fill="#fff">
        <path d="M18 6l14-5v44H18z"/><rect x="33" y="10" width="12" height="35"/>
        <path d="M2 22l14-4v27H2z"/>
        <g fill="var(--sky)"><rect x="5" y="26" width="8" height="2"/><rect x="5" y="31" width="8" height="2"/><rect x="5" y="36" width="8" height="2"/>
        <rect x="22" y="12" width="2" height="28"/><rect x="27" y="10" width="2" height="30"/></g>
      </svg>
      <p class="measure__text">Hotels &amp; tourist accomodation welcome guests again.</p>
    </div>
    <div class="measure measure--left" style="top:188px">
      <svg width="52" height="50" viewBox="0 0 52 50" fill="#fff">
        <path d="M4 2h44l4 10H0z"/><rect x="2" y="14" width="48" height="4"/>
        <rect x="14" y="28" width="24" height="4"/><rect x="24" y="32" width="4" height="16"/>
        <path d="M3 24v24M3 38h9v10" stroke="#fff" stroke-width="3" fill="none"/>
        <path d="M49 24v24M49 38h-9v10" stroke="#fff" stroke-width="3" fill="none"/>
      </svg>
      <p class="measure__text">Terraces re-open with a maximum occupncy of 30%.</p>
    </div>

    <div class="measure measure--right" style="top:18px">
      <p class="measure__text">Religious sites can be frequented again with maxim um capacity of 30%.</p>
      <svg width="54" height="54" viewBox="0 0 54 54" fill="var(--icon-navy)">
        <rect x="25" y="0" width="4" height="14"/><rect x="20" y="4" width="14" height="4"/>
        <path d="M27 14l14 12H13z"/><rect x="15" y="26" width="24" height="26"/>
        <path d="M2 36l11-6v22H2zM52 36l-11-6v22h11z"/>
        <path d="M22 52V42a5 5 0 0110 0v10z" fill="#fff"/>
        <rect x="5" y="40" width="5" height="4" fill="#fff"/><rect x="44" y="40" width="5" height="4" fill="#fff"/>
      </svg>
    </div>
    <div class="measure measure--right" style="top:105px">
      <p class="measure__text">Theaters, museums &amp; monuments open their doors with maximum capacity of 30%.</p>
      <svg width="54" height="46" viewBox="0 0 54 46" fill="var(--icon-navy)">
        <path d="M22 4c10-4 22-4 30 0v14c0 12-8 20-15 20s-15-8-15-20z"/>
        <path d="M2 14c9-3 19-3 26 0v14c0 10-7 17-13 17S2 38 2 28z" stroke="#fff" stroke-width="2"/>
      </svg>
    </div>
    <div class="measure measure--right" style="top:187px">
      <p class="measure__text">Events with maximum 50pax inside &amp; 400pax outside.</p>
      <svg width="50" height="50" viewBox="0 0 50 50" fill="none" stroke="var(--icon-navy)" stroke-width="2.4">
        <rect x="3" y="6" width="44" height="40" rx="3"/><path d="M3 15h44M12 2v8M25 2v8M38 2v8"/>
        <path d="M25 19l2 5h5l-4 3 2 5-5-3-5 3 2-5-4-3h5z" fill="var(--icon-navy)" stroke="none"/>
        <g fill="var(--icon-navy)" stroke="none">
          <rect x="8" y="24" width="4" height="4"/><rect x="38" y="24" width="4" height="4"/>
          <rect x="8" y="37" width="4" height="4"/><rect x="16" y="37" width="4" height="4"/><rect x="24" y="37" width="4" height="4"/><rect x="32" y="37" width="4" height="4"/><rect x="40" y="37" width="4" height="4"/>
        </g>
      </svg>
    </div>
  </section>

  <section class="highlights">
    <div class="highlights__rule" style="left:185px"></div>
    <div class="highlights__rule" style="left:348px"></div>

    <div class="highlight highlight--1">
      <svg width="46" height="48" viewBox="0 0 46 48" fill="var(--icon-light)">
        <path d="M16 12a7 7 0 0114 0" fill="none" stroke="var(--icon-light)" stroke-width="3"/>
        <path d="M6 12h28l4 32H2z"/>
        <circle cx="34" cy="32" r="10" fill="var(--icon-light)" stroke="var(--navy)" stroke-width="2"/>
        <path d="M29 37l10-10" stroke="var(--navy)" stroke-width="2"/>
        <circle cx="30" cy="28" r="1.8" fill="var(--navy)"/><circle cx="38" cy="36" r="1.8" fill="var(--navy)"/>
      </svg>
      <p class="highlight__text">All shops are back in business, with a maximum capacity of 50%.</p>
    </div>
    <div class="highlight highlight--2">
      <svg width="54" height="50" viewBox="0 0 54 50" fill="var(--icon-light)">
        <path d="M22 12c8-10 24-8 30 2z"/><path d="M36 10l-8 28" stroke="var(--icon-light)" stroke-width="3"/>
        <circle cx="12" cy="22" r="6"/>
        <g stroke="var(--icon-light)" stroke-width="2.5"><path d="M12 10v4M12 30v4M0 22h4M20 22h4M4 14l3 3M17 27l3 3M4 30l3-3M17 17l3-3"/></g>
        <path d="M2 40c6-4 14-4 20 0s14 4 20 0 10-2 12 0v3H2z"/>
        <path d="M6 47c6-3 12-3 18 0s12 3 18 0" fill="none" stroke="var(--icon-light)" stroke-width="2.5"/>
      </svg>
      <p class="highlight__text">Enjoj the beaches, at a safe distance from one another.</p>
    </div>
    <div class="highlight highlight--3">
      <svg width="50" height="48" viewBox="0 0 50 48" fill="var(--icon-light)">
        <path d="M25 10v10" stroke="var(--icon-light)" stroke-width="3"/>
        <circle cx="25" cy="8" r="4"/>
        <path d="M2 22h46l-4 8H6z"/><path d="M14 30h22l-3 16H17z"/>
      </svg>
      <p class="highlight__text">Meeting and conferences up to 80pax allowed.</p>
    </div>
  </section>

  <footer class="closing">WELCOME TO THE NEW NORMAL!</footer>
</main>
</body>
</html>
```